Wordpress Theme for Medical Clinics

** Please view updated Sitemap2.pdf doc to clarify some confusion ***

This is a multiuser WordPress subscription site for medical clinics. Please see attachment for sitemap. Please do not include extra content like social media icons, search bars, or images. If you have questions, please ask for clarification.
The site contains the following pages and sub-pages:

1. Home
2. Our Clinic
2a. Our Clinic > Mission
2b. Our Clinic > Services
2c. Our Clinic > Clinic Policies
2d. Our Clinic > Schedules
3. Our Staff
3a. Our Staff > [Staff member page]
4. Resources
4a. Resources > Patient Health (index)
4b. Resources > Patient Health (index) > [post]
4c. Resources > Links
4d. Resources > Forms
5. Alerts
5a. Alerts > [Alert Page]
6. Contact Us

Includes the Following Pages, Subpages, and Content
1. Home
a. About Us
b. Our Staff
c. Bulletins
d. Accepting New Patients (shown as an alert widget)
e. Links
i. Physician Toolbox
ii. Book an Appointment
f. Clinic Policies
i. Show first 3 policies (e.g. Late Arrivals, Missed Appointments, Fees)
ii. Link to Clinic Policies page
g. Primary widget (displayed on all pages)
i. Hours of operation
ii. Contact Info
1. Tel
2. Fax
3. Email
4. Address
5. Get directions (link to Google Maps)
2. Our Clinic
a. Main Page
i. Clinic Name
ii. Overview
iii. Languages Spoken
iv. Secondary Navigation
1. Mission
2. Services
3. Clinic Policies
4. Schedules (see attachment)
b. Our Clinic > Mission
c. Our Clinic > Services
i. For each service include service TITLE and DESCRIPTION
d. Our Clinic > Clinic Policies
i. For each policy include policy TITLE and DESCRIPTION
ii. Include the following policies in mockup
1. Late arrivals
2. Missed appointments
3. Fees for missed appointments
4. Referrals and follow-ups
5. Services not covered by RDA
6. Information for LTF patients
7. Medical Legal Reports
e. Our Clinic > Schedules
3. Our Staff
a. Main Page
i. Display a list of staff members. Include NAME and DESIGNATION
b. Our Staff > [Staff Name]
i. Include NAME, PICTURE, DESIGNATION, and BIO
4. Resources
a. Resources > Patient Health
i. Main Page
1. Posts (ordered by date)
a. Title
b. Summary
2. Side Navigation
a. Post Categories
ii. Patient Health > [post title]
1. Title
2. Post Category
3. Date
4. Author
5. Summary
6. Body
b. Resources > Links
1. Secondary Navigation - Categories
a. Sample Categories:
i. Local Services
ii. RDA and Drug Coverage
iii. Mental Health Resources
2. Category page
a. Include the following links in the 'Local Services' category
i. Hypertension clinics
ii. Home Care services
iii. Vaccine Clinics
c. Resources > Forms
i. Display a table with form TITLE and CATEGORY
ii. Side Navigation
1. Form Categories
a. Use the following sample Categories
i. Referrals
ii. Insurance
iii. Intake
iv. Discharge
v. Waivers
5. Alerts
a. Main page
i. List of all Alert posts
1. Include post TITLE as a link to the post
ii. Side Navigation
1. Alerts Archive
a. shown as Month + Number of posts
iii. Alerts > [Alert page]
1. Include TITLE, DATE, AUTHOR, BODY
6. Contact Us
a. Map
b. Hours of operation
c. Address
d. Phone number
e. Fax number
e. Fax number
f. Map
g. Email

Design notes:
- fixed width
- responsive (need designs for mobile, tablet, and desktop)
- simple, dark font, white background
- use Font Awesome icons where needed
- user adds own logo

Target Market(s)

Medical Clinics

Industry/Entity Type

Medical

Number of Pages Required

5+ page

Font styles to use
Serif
Sans Serif

Requirements
Must have
• Please keep designs very simple.
• Examples:
• https://www.quolbin.com/install
• http://www.ventrohax.com/company/about-us
• http://brindlequota.org/
• http://www.trosk.com/
Should not have
• Minimal or no use of shadows and gradients

```html
<!DOCTYPE html>
<html lang="en">
<head>
<meta charset="utf-8">
<title>Mivora Clinics</title>
<link href="https://fonts.googleapis.com/css2?family=Noticia+Text:wght@400;700&family=Open+Sans:wght@400;600;700&display=swap" rel="stylesheet">
<style>
:root{
  --teal:#5ec6cf;
  --teal-band:#74cfd8;
  --orange:#f47a55;
  --navy:#24506e;
  --ink:#222;
  --muted:#a9a9a9;
  --rule:#e3e3e3;
  --white:#fff;
}
*{box-sizing:border-box;margin:0;padding:0}
html,body{width:1200px;height:2281px;overflow:hidden;background:var(--white)}
body{position:relative;font-family:"Open Sans",sans-serif;color:var(--ink)}
.abs{position:absolute}
a{color:inherit;text-decoration:none}

/* top bar */
.topbar{position:absolute;left:0;top:0;width:1200px;height:50px;border-bottom:1px solid #eee}
.topbar .hours{left:49px;top:15px;font-size:13px;color:var(--muted)}
.topbar .emergency{left:768px;top:15px;font-size:13px;font-weight:700;color:var(--teal)}
.topbar .btn-ghost{top:9px;height:32px;border:1px solid #ddd;color:var(--orange);font-size:13px;display:flex;align-items:center;justify-content:center}

/* nav */
.mainnav{position:absolute;left:0;top:50px;width:1200px;height:79px;border-bottom:4px solid #d3eff2}
.brand{left:49px;top:20px;font-size:30px;font-weight:700;color:var(--orange);letter-spacing:-.5px}
.mainnav .item{top:30px;font-size:13px;color:#333;text-transform:uppercase}
.mainnav .item.active{color:var(--teal)}

/* hero */
.hero{position:absolute;left:0;top:129px;width:1200px;height:522px;overflow:hidden;
  background:linear-gradient(90deg,#d6eff2 0%,#c9e9ee 45%,#bfe2e8 100%)}
.hero .portrait{left:616px;top:-110px;width:780px;height:780px;border-radius:50%;
  background:linear-gradient(160deg,#f3f1ee 0%,#e2dcd6 45%,#c9c4c0 100%)}
.hero h1{left:180px;top:146px;font-family:"Noticia Text",serif;font-weight:700;font-size:31px;color:var(--navy)}
.hero h2{left:180px;top:184px;font-family:"Noticia Text",serif;font-weight:400;font-size:24px;color:#1f2c33}
.hero p{left:184px;top:228px;width:510px;font-size:12.5px;line-height:23px;color:#333}
.btn-orange{left:184px;top:320px;width:151px;height:47px;background:var(--orange);color:#fff;font-family:"Noticia Text",serif;font-weight:700;font-size:12px;display:flex;align-items:center;justify-content:center;box-shadow:0 2px 3px rgba(0,0,0,.15)}
.dots{display:flex;gap:9px}
.dots span{width:15px;height:15px;border-radius:50%;background:#fff}
.dots span.on{background:transparent;border:2px solid #fff}
.hero .dots span.on{background:var(--teal);border:3px solid #fff}

/* welcome + bulletins */
.sec-title{font-family:"Noticia Text",serif;font-weight:700;font-size:30px;color:var(--teal)}
.welcome-text{left:49px;width:570px;font-size:12.4px;line-height:22.8px;color:#222}
.btn-navy{width:150px;height:47px;background:var(--navy);color:#fff;font-family:"Noticia Text",serif;font-weight:700;font-size:12px;display:flex;align-items:center;justify-content:center;box-shadow:0 2px 3px rgba(0,0,0,.2)}
.bulletin{left:700px;width:451px;height:167px;border-bottom:1px solid var(--rule)}
.bulletin .thumb{left:1px;top:0;width:163px;height:114px;border:4px solid #fff;box-shadow:0 1px 4px rgba(0,0,0,.25);
  background:linear-gradient(135deg,#c7d3de,#e7e2dc 55%,#9fb0c2)}
.bulletin h3{left:190px;top:-4px;font-weight:400;font-size:23px;color:#222}
.bulletin .date{left:193px;top:36px;font-size:11.5px;color:var(--orange);display:flex;align-items:center;gap:8px}
.bulletin p{left:190px;top:64px;width:260px;font-size:12px;line-height:22px;color:#222}

/* testimonial */
.testimonial{position:absolute;left:0;top:1212px;width:1200px;height:320px;background:var(--teal-band);color:#fff;text-align:center}
.testimonial .quote{left:0;width:1200px;top:28px;font-family:"Noticia Text",serif;font-weight:700;font-size:56px;color:var(--navy);line-height:1}
.testimonial h2{left:0;width:1200px;top:92px;font-family:"Noticia Text",serif;font-weight:700;font-size:30px}
.testimonial p{left:0;width:1200px;top:149px;font-size:17px;color:#f2fbfc}
.testimonial .author{left:491px;width:189px;top:214px;display:flex;align-items:center;gap:14px;font-size:11px;font-weight:700}
.testimonial .author i{flex:1;height:1px;background:#fff}

/* staff */
.staff-card{top:1650px;width:240px;text-align:center}
.staff-card .avatar{width:220px;height:220px;margin:0 auto;border-radius:50%;border:9px solid #eeeeee;
  background:linear-gradient(180deg,#eef2f5 0%,#d9e1e8 60%,#c5d2dc 100%)}
.staff-card h4{margin-top:28px;font-size:14px;font-weight:700;text-transform:uppercase;color:#222}
.staff-card .role{margin-top:8px;font-size:17px;color:var(--teal)}
.staff-card .social{margin-top:10px;display:flex;justify-content:center;gap:5px}
.staff-card .social span{width:17px;height:17px;border-radius:50%;background:#c4c4c4}

/* book band */
.book{position:absolute;left:0;top:2046px;width:1200px;height:141px;background:var(--teal-band);display:flex;align-items:center;justify-content:center;gap:38px;color:#fff;font-size:34px;font-weight:700}
.book .phone{display:flex;align-items:center;gap:6px}

/* footer */
.footer{position:absolute;left:0;top:2187px;width:1200px;height:94px;background:var(--navy);color:#fff}
.footer .links{left:49px;top:23px;font-size:12px;display:flex;gap:0}
.footer .links span.sep{margin:0 15px}
.footer .copy{left:49px;top:51px;font-size:11.5px;color:#d9e3ea}
.footer .toolbox{left:961px;top:23px;width:165px;height:53px;border:1px solid #fff;font-size:12px;font-weight:600;display:flex;align-items:center;justify-content:center}
</style>
</head>
<body>

<header class="topbar">
  <span class="abs hours">Opening Hours: Monday to Saturday - 8am to 9pm.</span>
  <span class="abs emergency">Emergency call: 000-555-0142</span>
  <a class="abs btn-ghost" style="left:993px;width:73px">Login</a>
  <a class="abs btn-ghost" style="left:1077px;width:74px">Signup</a>
</header>

<nav class="mainnav">
  <span class="abs brand">Mivora Clinics</span>
  <a class="abs item active" style="left:498px">Home</a>
  <a class="abs item" style="left:581px">Clinic</a>
  <a class="abs item" style="left:666px">Our Staff</a>
  <a class="abs item" style="left:778px">Resources</a>
  <a class="abs item" style="left:895px">Contact Us</a>
  <a class="abs item" style="left:1019px">Login</a>
  <a class="abs item" style="left:1103px">Signup</a>
</nav>

<section class="hero" role="img" aria-label="Soft blurred clinic interior in pale blue tones">
  <div class="abs portrait" role="img" aria-label="Photo of a smiling doctor in a white coat with a stethoscope"></div>
  <h1 class="abs">You Need a Professional</h1>
  <h2 class="abs">Give us a call to discuss how we can help you</h2>
  <p class="abs">Nisi elit consequat ipsum, nec sagittis sem nibh id elit. Duis sed odio sit amet nibh vulputate cursus a sit amet mauris. Morbi accumsan ipsum velit. Nam nec tellus a odio tincidunt auctor a ornare odio.</p>
  <a class="abs btn-orange">LEARN MORE</a>
  <div class="abs dots" style="left:556px;top:488px"><span class="on"></span><span></span><span></span><span></span></div>
</section>

<h2 class="abs sec-title" style="left:49px;top:684px">Welcome to Our Clinic</h2>
<p class="abs welcome-text" style="top:757px">Aenean sollicitudin, lorem quis bibendum auctor, nisi elit consequat ipsum, nec sagittis sem nibh id elit. Duis sed odio sit amet nibh vulputate cursus a sit amet mauris. Morbi accumsan ipsum velit. Nam nec tellus a odio tincidunt auctor a ornare odio. Sed non&nbsp; mauris vitae erat consequat auctor eu in elit. Class aptent taciti sociosqu ad litora torquent per conubia nostra, per inceptos himenaeos. Mauris in erat justo. Nullam ac urna eu felis dapibus condimentum sit amet a augue. Sed non neque elit. Sed ut imperdiet nisi. Proin condimentum.</p>
<p class="abs welcome-text" style="top:927px">Etiam pharetra, erat sed fermentum feugiat velit mauris egestas quam, ut aliquam massa nisl quis neque. Suspendisse in orci enim.This is Pixelform's version&nbsp; of Lorem Ipsum. Proin gravida nibh vel velit auctor aliquet. Aenean sollicitudin, lorem quis bibendum auctor, nisi elit consequat ipsum, nec sagittis sem nibh id elit. Duis sed odio sit amet nibh vulputate cursus a sit amet mauris. Morbi accumsan ipsum velit. Nam nec tellus a odio tincidunt auctor a ornare odio. Sed non&nbsp; mauris vitae erat consequat auctor eu in elit. Class aptent taciti sociosqu ad litora torquent.</p>
<a class="abs btn-navy" style="left:49px;top:1106px">LEARN MORE</a>

<h2 class="abs sec-title" style="left:700px;top:684px">Bulletins</h2>
<article class="abs bulletin" style="top:764px">
  <div class="abs thumb" role="img" aria-label="Photo of a doctor consulting with a patient"></div>
  <h3 class="abs">Easy To Access</h3>
  <span class="abs date"><svg width="12" height="12" viewBox="0 0 12 12"><rect x="0.5" y="1.5" width="11" height="10" fill="none" stroke="#f47a55"/><rect x="0.5" y="1.5" width="11" height="3" fill="#f47a55"/></svg>24 Jan 2015</span>
  <p class="abs">Aenean sollicitudin, lorem quis bibendum auctor, nisi elit consequat ...</p>
</article>
<article class="abs bulletin" style="top:931px">
  <div class="abs thumb" role="img" aria-label="Photo of a doctor with a mother and child"></div>
  <h3 class="abs">Easy To Access</h3>
  <span class="abs date"><svg width="12" height="12" viewBox="0 0 12 12"><rect x="0.5" y="1.5" width="11" height="10" fill="none" stroke="#f47a55"/><rect x="0.5" y="1.5" width="11" height="3" fill="#f47a55"/></svg>24 Jan 2015</span>
  <p class="abs">Aenean sollicitudin, lorem quis bibendum auctor, nisi elit consequat ...</p>
</article>
<a class="abs btn-navy" style="left:703px;top:1107px">VIEW ALL</a>

<section class="testimonial">
  <span class="abs quote">&ldquo;</span>
  <h2 class="abs">What Our Happy Patients Say</h2>
  <p class="abs">I received the best care ever! The doctors and the nurses are the best of those I ever met.</p>
  <div class="abs author"><i></i>TOBIN<i></i></div>
  <div class="abs dots" style="left:553px;top:255px"><span class="on"></span><span></span><span></span><span></span></div>
</section>

<h2 class="abs sec-title" style="left:0;width:1200px;text-align:center;top:1562px">Meet Our Staff</h2>
<div class="abs staff-card" style="left:151px">
  <div class="avatar" role="img" aria-label="Portrait photo of a male doctor"></div>
  <h4>Reid Calloway</h4><div class="role">Doctor</div>
  <div class="social"><span></span><span></span><span></span></div>
</div>
<div class="abs staff-card" style="left:479px">
  <div class="avatar" role="img" aria-label="Portrait photo of a female therapist"></div>
  <h4>Nora Tessel</h4><div class="role">Therapist</div>
  <div class="social"><span></span><span></span><span></span></div>
</div>
<div class="abs staff-card" style="left:806px">
  <div class="avatar" role="img" aria-label="Portrait photo of a male doctor in scrubs"></div>
  <h4>Ilse Marwood</h4><div class="role">Doctor</div>
  <div class="social"><span></span><span></span><span></span></div>
</div>

<section class="book">
  <span>Book an Appointment</span>
  <span class="phone">
    <svg width="40" height="40" viewBox="0 0 40 40"><circle cx="20" cy="20" r="18" fill="none" stroke="#fff" stroke-width="3"/><path d="M13 11c2-1 3 0 4 2l1 3c0 1-1 2-2 3 1 3 3 5 6 6 1-1 2-2 3-2l3 1c2 1 3 2 2 4-1 2-3 3-5 2-7-2-12-7-14-14-1-2 0-4 2-5z" fill="#fff"/></svg>
    800-555-0187
  </span>
</section>

<footer class="footer">
  <nav class="abs links">
    <a>Home</a><span class="sep">|</span><a>Clinic</a><span class="sep">|</span><a>Our Staff</a><span class="sep">|</span><a>Resources</a><span class="sep">|</span><a>Contact us</a><span class="sep">|</span><a>Login</a><span class="sep">|</span><a>Signup</a>
  </nav>
  <p class="abs copy">© 2015 All Rights Reserved. Terms of use and Privacy Policy</p>
  <a class="abs toolbox">PHYSICIAN TOOLBOX</a>
</footer>

</body>
</html>
```